Hall of Fame annnouncement graphic for social media

I need a social media Hall of Fame announcement designed in the styles of some of the examples I've posted. I have attached the two gentlemens head shots ... the names are Dale Brinton and Ray Pemberly

It is for the BRAXWOOD LINKS HONOR GALLERY also include 2026 Inductees ... I have also attached the logo... make the post in similar colors as the logo.

I need this tomorrow so I am going to pick a winner in the next 24 hours.

```html
<!DOCTYPE html>
<html lang="en">
<head>
<meta charset="utf-8">
<title>Braxwood Links Honor Gallery – 2026 Inductees</title>
<link rel="stylesheet" href="https://fonts.googleapis.com/css2?family=Great+Vibes&family=Montserrat:wght@500;600;700&family=Oswald:wght@700&display=swap">
<style>
  :root{
    --navy:#15225a;
    --navy-deep:#0f1a48;
    --navy-soft:#3b4f86;
    --red:#b41c0c;
    --red-deep:#8f1509;
    --white:#ffffff;
    --silver-light:#f4f5f7;
    --silver:#bfc1c5;
  }
  html,body{margin:0;padding:0;width:1200px;height:1200px;overflow:hidden;background:var(--white);}
  .announcement{display:block;width:1200px;height:1200px;}
  .brand-name{font-family:"Montserrat",sans-serif;font-weight:700;fill:var(--navy);letter-spacing:3px;}
  .title-vertical{font-family:"Oswald",sans-serif;font-weight:700;fill:var(--white);}
  .title-main{font-family:"Montserrat",sans-serif;font-weight:500;}
  .year-line{font-family:"Great Vibes",cursive;fill:var(--white);}
  .inductee-name{font-family:"Montserrat",sans-serif;font-weight:600;fill:var(--white);letter-spacing:0.5px;}
</style>
</head>
<body>
<svg class="announcement" viewBox="0 0 1200 1200" xmlns="http://www.w3.org/2000/svg">
  <defs>
    <linearGradient id="scene-tone" x1="0" y1="0" x2="1" y2="1">
      <stop offset="0" stop-color="#42578f"/>
      <stop offset="0.45" stop-color="#23336b"/>
      <stop offset="1" stop-color="#101b4a"/>
    </linearGradient>
    <linearGradient id="silver-fill" x1="0" y1="0" x2="1" y2="0">
      <stop offset="0" stop-color="var(--silver)"/>
      <stop offset="0.4" stop-color="var(--silver-light)"/>
      <stop offset="0.6" stop-color="var(--white)"/>
      <stop offset="1" stop-color="var(--silver)"/>
    </linearGradient>
    <radialGradient id="portrait-tone" cx="0.5" cy="0.4" r="0.6">
      <stop offset="0" stop-color="#e9dcd6"/>
      <stop offset="0.6" stop-color="#c84a3a"/>
      <stop offset="1" stop-color="var(--red-deep)"/>
    </radialGradient>
  </defs>

  <!-- background -->
  <rect class="scene-backdrop" x="0" y="0" width="1200" height="1200" fill="url(#scene-tone)" role="img" aria-label="Clubhouse and landscaped entrance walkway, tinted navy"/>

  <!-- white header shape -->
  <path class="header-panel" d="M0 0 H1200 V21 H880 C790 21 760 60 720 110 C680 160 650 210 560 210 H0 Z" fill="var(--white)"/>

  <!-- brand -->
  <g class="brand">
    <text class="brand-name" x="76" y="100" font-size="34">BRAXWOOD LINKS</text>
    <text class="brand-name" x="76" y="142" font-size="34">HONOR GALLERY</text>
    <circle cx="490" cy="118" r="10" fill="var(--red)"/>
  </g>

  <!-- headline -->
  <text class="title-vertical" transform="translate(164 596) rotate(-90)" font-size="122" textLength="351" lengthAdjust="spacingAndGlyphs">HALL OF</text>
  <text class="title-main" x="183" y="508" font-size="372" fill="url(#silver-fill)" textLength="944" lengthAdjust="spacingAndGlyphs">FAME</text>

  <rect class="accent-rule" x="187" y="557" width="348" height="9" fill="var(--red)"/>
  <text class="year-line" x="554" y="584" font-size="84" textLength="577" lengthAdjust="spacingAndGlyphs">2026 Inductees</text>

  <!-- inductee portraits -->
  <g class="portrait">
    <circle cx="348" cy="905" r="183" fill="none" stroke="var(--white)" stroke-width="3"/>
    <circle cx="348" cy="905" r="168" fill="url(#portrait-tone)" role="img" aria-label="Head-and-shoulders photo of Dale Brinton in a white polo"/>
  </g>
  <g class="portrait">
    <circle cx="852" cy="905" r="183" fill="none" stroke="var(--white)" stroke-width="3"/>
    <circle cx="852" cy="905" r="168" fill="url(#portrait-tone)" role="img" aria-label="Head-and-shoulders photo of Ray Pemberly in a light pink polo"/>
  </g>

  <!-- name band -->
  <rect class="name-band" x="0" y="1108" width="1200" height="52" fill="var(--red)"/>
  <text class="inductee-name" x="348" y="1148" font-size="39" text-anchor="middle">DALE BRINTON</text>
  <text class="inductee-name" x="852" y="1148" font-size="39" text-anchor="middle">RAY PEMBERLY</text>
</svg>
</body>
</html>
```